Stationery Design Project

Fire and building compliance company needs business card, letterhead and complement slip designed.
Have included a brief about business card, basic want front keep quite clean with just the KTV logo and the words Marlowby Alarm and Guard 2012 Ltd (small print) along the bottom. Website needs to be included (www.ktvalarm.example.nz) on either front or back.
The info for back is as per attachment.
Letterhead and complement slip should have the usual stuff KTV logo etc and also the accredited test lab logo at the bottom (can be small size)
Target Market(s)
Property owners, buisness managers
Industry/Entity Type
Building
Look and feel
Each slider illustrates characteristics of the customer's brand and the style your logo design should communicate.

```html
<!DOCTYPE html>
<html lang="en">
<head>
<meta charset="utf-8">
<title>KTV Stationery</title>
<link href="https://fonts.googleapis.com/css2?family=Open+Sans:wght@400;600;700&family=Caveat:wght@400&display=swap" rel="stylesheet">
<style>
  :root {
    --canvas: #e8e8e8;
    --paper: #ffffff;
    --ink: #3d3d3d;
    --ink-soft: #555555;
    --brand-blue: #1f6f9a;
    --brand-orange: #f07a1e;
    --card-blue: #1a8fd6;
    --card-blue-light: #6fbde8;
    --edge: #d6d6d6;
  }
  * { box-sizing: border-box; margin: 0; padding: 0; }
  html, body { width: 1200px; height: 800px; overflow: hidden; }
  body {
    background: var(--canvas);
    font-family: "Open Sans", Arial, sans-serif;
    color: var(--ink);
    position: relative;
  }
  .sheet {
    position: absolute;
    background: var(--paper);
    border: 1px solid var(--edge);
  }

  /* Brand lockup */
  .brand { position: absolute; display: flex; align-items: flex-start; gap: 6px; }
  .brand-dot { border-radius: 50%; background: var(--brand-orange); flex: none; }
  .brand-name { font-weight: 600; color: var(--ink); letter-spacing: 0.5px; line-height: 1; }
  .brand-tag { color: var(--ink-soft); line-height: 1.05; }

  /* Letterhead */
  .letterhead { left: 145px; top: 75px; width: 475px; height: 640px; }
  .letterhead .brand { left: 26px; top: 14px; }
  .letterhead .brand-dot { width: 34px; height: 34px; }
  .letterhead .brand-name { font-size: 20px; }
  .letterhead .brand-tag { font-size: 7px; }
  .letterhead-contact {
    position: absolute; right: 22px; top: 26px;
    text-align: right; font-size: 5.5px; line-height: 1.45; color: var(--ink);
    font-weight: 600;
  }
  .letterhead-contact .gap { height: 6px; }

  /* Compliment slips */
  .slip { width: 500px; height: 240px; }
  .slip-back { left: 490px; top: 168px; }
  .slip-front { left: 572px; top: 230px; width: 494px; height: 236px; }
  .slip .brand { left: 6px; top: 10px; }
  .slip .brand-dot { width: 44px; height: 44px; margin-top: 4px; }
  .slip .brand-name { font-size: 25px; }
  .slip .brand-tag { font-size: 9.5px; }
  .slip-greeting {
    position: absolute; left: 56px; bottom: 6px;
    font-family: "Caveat", cursive; font-size: 17px; color: var(--ink);
  }
  .slip-back .slip-greeting { left: 62px; }
  .slip-footer {
    position: absolute; right: 6px; bottom: 5px;
    font-size: 4.8px; color: var(--ink-soft); white-space: nowrap;
  }

  /* Business cards */
  .card { position: absolute; border: 1px solid var(--edge); }
  .card-back {
    left: 408px; top: 555px; width: 207px; height: 120px;
    background: var(--paper);
  }
  .card-back-panel {
    position: absolute; left: 90px; top: 0; right: 0; bottom: 0;
    background: var(--card-blue);
  }
  .card-back-name {
    position: absolute; left: 110px; top: 16px;
    font-weight: 600; font-size: 20px; color: var(--paper); letter-spacing: 0.5px;
  }
  .accredit-badge {
    position: absolute; left: 5px; bottom: 16px;
    width: 10px; height: 12px; background: var(--ink-soft);
  }

  .card-front {
    left: 432px; top: 590px; width: 205px; height: 110px;
    background: var(--paper);
  }
  .card-stripe {
    position: absolute; left: 0; top: 0; right: 0; height: 6px;
    background: linear-gradient(90deg, var(--card-blue-light), var(--card-blue));
  }
  .person { position: absolute; left: 8px; top: 40px; }
  .person-name { font-size: 15px; line-height: 1; color: var(--card-blue); font-weight: 600; letter-spacing: -0.3px; }
  .person-name b { color: var(--ink); font-weight: 700; }
  .person-company { font-size: 5.5px; color: var(--ink-soft); margin-top: 2px; }
  .person-contact { font-size: 4.3px; line-height: 1.4; color: var(--ink-soft); margin-top: 5px; }
  .services { position: absolute; left: 118px; top: 28px; width: 86px; }
  .services-title { font-size: 4.8px; color: var(--ink); margin-bottom: 7px; }
  .services-list { list-style: none; font-size: 3.6px; line-height: 1; color: var(--ink); }
  .services-list li { margin-bottom: 5.6px; white-space: nowrap; }
</style>
</head>
<body>

  <!-- Letterhead -->
  <section class="sheet letterhead">
    <div class="brand">
      <span class="brand-dot"></span>
      <div>
        <div class="brand-name">KTV</div>
        <div class="brand-tag">Fire and Building<br>Compliance</div>
      </div>
    </div>
    <address class="letterhead-contact" style="font-style:normal">
      Marlowby Alarm and Guard<br>
      12 Harbour Lane Extension,<br>
      Ashford, 4100
      <div class="gap"></div>
      Phone: 06 555 0140<br>
      Fax: 06 555 0172<br>
      Email: admin@ktvalarm.example.nz
    </address>
  </section>

  <!-- Compliment slip (rear) -->
  <section class="sheet slip slip-back">
    <div class="brand">
      <span class="brand-dot"></span>
      <div>
        <div class="brand-name">KTV</div>
        <div class="brand-tag">Fire and Building<br>Compliance</div>
      </div>
    </div>
    <p class="slip-greeting">With Compliments</p>
  </section>

  <!-- Compliment slip (front) -->
  <section class="sheet slip slip-front">
    <div class="brand">
      <span class="brand-dot"></span>
      <div>
        <div class="brand-name">KTV</div>
        <div class="brand-tag">Fire and Building<br>Compliance</div>
      </div>
    </div>
    <p class="slip-greeting">With Compliments</p>
    <p class="slip-footer">12 Harbour Lane Extension, Ashford, 4100 - Phone: 06 555 0140 - Fax: 06 555 0172 - Email: admin@ktvalarm.example.nz</p>
  </section>

  <!-- Business card (brand side) -->
  <section class="card card-back">
    <span class="accredit-badge"></span>
    <div class="card-back-panel"></div>
    <div class="card-back-name">KTV</div>
  </section>

  <!-- Business card (details side) -->
  <section class="card card-front">
    <div class="card-stripe"></div>
    <div class="person">
      <div class="person-name">John<b>DOE</b></div>
      <div class="person-company">Marlowby Alarm and Guard</div>
      <div class="person-contact">
        12 Harbour Lane Extension,<br>
        Ashford, 4100<br>
        Phone: 06 555 0140<br>
        Fax: 06 555 0172<br>
        Email: admin@ktvalarm.example.nz
      </div>
    </div>
    <div class="services">
      <div class="services-title">OUR SERVICES</div>
      <ul class="services-list">
        <li>Building compliance specialists</li>
        <li>Building warrant of fitness preparation</li>
        <li>Fire alarms, Fire Extinguishers &amp; emergency lighting</li>
        <li>Approved evacuation schemes</li>
        <li>Pressure testing LPG CNG Fire extinguishers</li>
        <li>Security alarm and CCTV systems</li>
      </ul>
    </div>
  </section>

</body>
</html>
```